Marwick Jewelers New Website Design

This project is to provide a new design for an existing website. The existing website is marwickjewelers dot com . I have created a overview document that outlines all the details for the project. I do not need the design to be converted into HTML. I have a team for that already so please don't ask. I have a lot of images .. too many to upload here so they are on my dev server located at quillfoxstudio com slash marwick slash assets

Number of Pages Required

1 page

```html
<!DOCTYPE html>
<html lang="en">
<head>
<meta charset="utf-8">
<title>Marwick Jewelers</title>
<link href="https://fonts.googleapis.com/css2?family=Great+Vibes&family=Roboto:wght@400;500;700&display=swap" rel="stylesheet">
<style>
:root{
  --teal:#5a9aa1;
  --teal-dark:#4d8b92;
  --ink:#1e1e1e;
  --text:#444;
  --night:#0b1014;
  --white:#fff;
  --line:#e3e3e3;
}
*{box-sizing:border-box;margin:0;padding:0}
html,body{width:1200px;height:3669px;overflow:hidden}
body{font-family:'Roboto',sans-serif;color:var(--ink);background:var(--white);position:relative}
.abs{position:absolute}
.script{font-family:'Great Vibes',cursive;color:var(--teal);font-weight:400}
.btn{position:absolute;display:flex;align-items:center;justify-content:center;background:var(--teal);color:var(--white);font-weight:700;font-size:15px;border-radius:26px}

/* header */
.brand{left:111px;top:40px;width:160px;font-size:26px;font-weight:500;color:var(--ink);line-height:1.15;text-align:center}
.brand small{display:block;font-size:10px;letter-spacing:7px;color:#999;margin-top:8px}
.topbar{top:28px;left:423px;display:flex;align-items:center;gap:16px;font-size:15px}
.ic{width:46px;height:46px;border:2px solid var(--teal);border-radius:50%;display:flex;align-items:center;justify-content:center}
.topbar .lbl{color:var(--teal)}
.topbar .val{color:#333}
.sep{width:1px;height:24px;background:#ccc;margin:0 8px}
.dot{width:12px;height:12px;border-radius:50%;background:var(--teal)}
.nav{top:103px;left:298px;width:790px;display:flex;justify-content:space-between;font-size:14px;font-weight:500}

/* hero */
.hero{top:157px;left:0;width:1200px;height:670px}
.hero-title{left:111px;top:300px;font-size:86px;color:var(--white);font-family:'Great Vibes',cursive;white-space:nowrap}
.hero-copy{left:111px;top:437px;width:470px;color:var(--white);font-size:14.5px;line-height:26px}
.slides{top:741px;left:570px;display:flex;gap:8px;align-items:center}
.slides span{width:11px;height:11px;border-radius:50%;background:var(--white)}
.slides .on{width:18px;height:18px;border:3px solid var(--white);background:var(--teal)}

/* about */
.about-text{left:606px;top:910px;width:480px}
.about-text h2{font-size:31px;font-weight:500;line-height:43px;margin-top:4px}
.about-text p{font-size:14px;line-height:26px;color:var(--text);text-align:justify;margin-top:22px}

/* products */
.products{top:1391px;left:0;width:1200px;height:601px;background:var(--teal)}
.center{width:1200px;text-align:center;left:0}
.products h2,.contact h2{font-size:31px;font-weight:500;color:var(--white)}
.prod-card{top:205px;width:303px;height:234px;background:var(--white);border-radius:4px}
.prod-name{top:463px;width:303px;text-align:center;color:var(--white);font-size:25px;font-weight:500}
.prod-price{top:504px;width:303px;text-align:center;color:var(--white);font-size:18px;font-weight:700}
.arrow{top:305px;width:36px;height:36px;border:2px solid var(--white);border-radius:50%;display:flex;align-items:center;justify-content:center}

/* design */
.design-intro{top:2185px;left:290px;width:620px;text-align:center;font-size:15px;line-height:26px;color:#333}
.design-card{top:2262px;width:228px;height:310px;background:var(--white);box-shadow:0 2px 10px rgba(0,0,0,.12);border-radius:3px;overflow:hidden;text-align:center}
.design-card .photo{height:172px}
.design-card h3{font-size:18px;font-weight:700;line-height:30px;margin-top:14px;padding:0 12px}
.design-card a{display:block;margin-top:8px;font-size:14px;color:var(--teal);text-decoration:underline;font-weight:500}

/* contact */
.contact{top:2742px;left:559px;width:641px;height:514px;background:var(--teal)}
.field{position:absolute;background:var(--white);border-radius:3px;font-size:14px;color:#999;padding:14px 13px;display:flex;justify-content:space-between;align-items:flex-start}
.submit{position:absolute;left:223px;top:420px;width:135px;height:50px;border:2px solid var(--white);border-radius:26px;color:var(--white);font-weight:700;font-size:15px;display:flex;align-items:center;justify-content:center}

/* footer */
.fcol{top:3348px}
.fcol h4{font-size:20px;font-weight:500;margin-bottom:14px}
.fcol li{list-style:none;font-size:13px;line-height:23px;color:#444}
.fcol p{font-size:14px;line-height:23px;color:#444}
.copy{top:3612px;left:111px;font-size:14px;color:#777}
.copy b{color:var(--ink)}
</style>
</head>
<body>

<!-- header -->
<div class="abs brand">Marwick<small>JEWELERS</small></div>
<div class="abs topbar">
  <div class="ic"><svg width="18" height="18" viewBox="0 0 24 24"><path fill="#5a9aa1" d="M6.6 10.8a15 15 0 0 0 6.6 6.6l2.2-2.2c.3-.3.7-.4 1-.2 1.1.4 2.3.6 3.6.6.6 0 1 .4 1 1V20c0 .6-.4 1-1 1A17 17 0 0 1 3 4c0-.6.4-1 1-1h3.5c.6 0 1 .4 1 1 0 1.3.2 2.5.6 3.6.1.3 0 .7-.2 1z"/></svg></div>
  <div><span class="lbl">Phone : </span><span class="val">555-014-3870</span></div>
  <div class="sep"></div>
  <div class="ic"><svg width="18" height="14" viewBox="0 0 24 18"><path fill="#5a9aa1" d="M0 2l12 8 12-8V0H0zm0 3v13h24V5l-12 8z"/></svg></div>
  <div><span class="lbl">Email : </span><span class="val">info@marwickjewelers.com</span></div>
  <div class="sep"></div>
  <div class="dot"></div><div class="dot" style="margin-left:14px"></div>
</div>
<nav class="abs nav">
  <span>Company</span><span>Custom Jewelery Services ▾</span><span>Jewelery Repair Services</span><span>Resources</span><span>Showcase</span><span>Gallery</span><span>More ▾</span>
</nav>

<!-- hero -->
<section class="abs hero">
  <svg width="1200" height="670" viewBox="0 0 1200 670" style="position:absolute;left:0;top:0">
    <defs>
      <radialGradient id="pearl" cx="50%" cy="45%" r="55%">
        <stop offset="0" stop-color="#8fb3b0"/><stop offset=".6" stop-color="#3a4a4d"/><stop offset="1" stop-color="#0b1014"/>
      </radialGradient>
    </defs>
    <path d="M0 0H1200V555C900 640 620 665 440 660 260 655 120 620 0 555Z" fill="#5a9aa1"/>
    <path d="M0 0H1200V543C900 625 620 650 440 645 260 640 120 610 0 555Z" fill="#0b1014"/>
    <rect x="600" y="140" width="440" height="440" fill="url(#pearl)" role="img" aria-label="Photo of a silver ring set with a grey pearl and small diamonds"/>
  </svg>
  <div class="abs hero-title">Marwick Jewelers</div>
  <p class="abs hero-copy">From “will you?” to “I do” and every momentous occasion in between, Marwick Jewelers offers a radiant array of elegant stones and settings to take her breath away.</p>
  <div class="btn" style="left:111px;top:386px;width:135px;height:50px">Contact Us</div>
  <div class="abs slides" style="top:584px"><span></span><span class="on"></span><span></span></div>
</section>

<!-- about -->
<svg class="abs" style="left:118px;top:924px" width="410" height="410" viewBox="0 0 410 410">
  <circle cx="204" cy="204" r="204" fill="#5a9aa1"/>
  <circle cx="218" cy="210" r="191" fill="#3a2a26" role="img" aria-label="Photo of a rose gold coil ring with a diamond flower"/>
</svg>
<div class="abs about-text">
  <div class="script" style="font-size:40px">About Us</div>
  <h2>Jewelry Crafted with Decades of Experience</h2>
  <p>Marwick Jewelers is an independent, family owned jewelry store located in the heart of Downtown Harrowgate. Owner, Daniel Marwick has been with the business since 1990. His wife, Helen, joined the business in 2010, store manager, Tom, came on board in 2016 and Lucia joined the team in 2021. Marwick Jewelers specializes in engagement rings, fashion jewelry and custom designed pieces.Whether you want to create the ring of your dreams or re-create a family heirloom, Marwick Jewelers is the place to go.</p>
</div>
<div class="btn" style="left:607px;top:1255px;width:135px;height:50px">Learn More</div>

<!-- products -->
<section class="abs products">
  <div class="abs center script" style="top:70px;font-size:40px;color:var(--white)">Products</div>
  <h2 class="abs center" style="top:117px">Features Items</h2>
  <div class="abs arrow" style="left:53px"><svg width="10" height="14" viewBox="0 0 10 14"><path d="M8 1L2 7l6 6" stroke="#fff" stroke-width="2" fill="none"/></svg></div>
  <div class="abs arrow" style="left:1110px"><svg width="10" height="14" viewBox="0 0 10 14"><path d="M2 1l6 6-6 6" stroke="#fff" stroke-width="2" fill="none"/></svg></div>
  <div class="abs prod-card" style="left:111px;background:linear-gradient(#fff,#eceff1)" role="img" aria-label="Photo of a steel watch"></div>
  <div class="abs prod-card" style="left:448px;background:radial-gradient(circle,#f6eef2,#fff 70%)" role="img" aria-label="Photo of a gold ring with a pearl"></div>
  <div class="abs prod-card" style="left:785px;background:radial-gradient(circle,#f3e8ee,#fff 70%)" role="img" aria-label="Photo of a gold and diamond ring"></div>
  <div class="abs prod-name" style="left:111px">Marwick Watch</div>
  <div class="abs prod-name" style="left:448px">Gold + Pearl Rings</div>
  <div class="abs prod-name" style="left:785px">Gold + Diamond Rings</div>
  <div class="abs prod-price" style="left:111px">$250</div>
  <div class="abs prod-price" style="left:448px">$250</div>
  <div class="abs prod-price" style="left:785px">$250</div>
</section>

<!-- design -->
<div class="abs center script" style="top:2072px;font-size:40px">Design</div>
<h2 class="abs center" style="top:2124px;font-size:31px;font-weight:500">Custom Design</h2>
<p class="abs design-intro">We like to say, "If you can dream it, we can make it!" If you've seen a ring or other piece of jewelry you like, we can recreate it.</p>
<div class="abs design-card" style="left:111px"><div class="photo" style="background:linear-gradient(#e6d6b4,#cbb48c)" role="img" aria-label="Photo of a dragonfly pendant"></div><h3>Custom Dragonfly Pendant</h3><a>Learn More</a></div>
<div class="abs design-card" style="left:361px"><div class="photo" style="background:linear-gradient(#f2eee8,#dcd5cb)" role="img" aria-label="Photo of a fox pendant"></div><h3>Custom Fox Pendant</h3><a>Learn More</a></div>
<div class="abs design-card" style="left:611px"><div class="photo" style="background:linear-gradient(#4b4f52,#b9b3ad)" role="img" aria-label="Photo of a pink coral ring"></div><h3>Custom Pink Coral and Am</h3><a>Learn More</a></div>
<div class="abs design-card" style="left:861px"><div class="photo" style="background:linear-gradient(#3e3a36,#8a7565)" role="img" aria-label="Photo of a rose gold engagement ring"></div><h3>Custom Rose Gold Engagem</h3><a>Learn More</a></div>
<div class="btn" style="left:532px;top:2604px;width:135px;height:50px">View All</div>

<!-- map + contact -->
<div class="abs" style="left:0;top:2742px;width:559px;height:514px;background:linear-gradient(135deg,#eef0f1,#e2e5e7)" role="img" aria-label="Street map showing the store location"></div>
<section class="abs contact">
  <div class="abs script" style="left:0;width:641px;text-align:center;top:50px;font-size:40px;color:var(--white)">Get in Touch</div>
  <h2 class="abs" style="left:0;width:641px;text-align:center;top:95px">Contact Us</h2>
  <div class="field" style="left:43px;top:148px;width:243px;height:46px">First name<span>●</span></div>
  <div class="field" style="left:290px;top:148px;width:238px;height:46px">Last name<span>●</span></div>
  <div class="field" style="left:43px;top:210px;width:243px;height:46px">Phone<span>☎</span></div>
  <div class="field" style="left:290px;top:210px;width:238px;height:46px">Email<span>✉</span></div>
  <div class="field" style="left:43px;top:273px;width:485px;height:115px">Message</div>
  <div class="submit" style="left:223px;top:420px">Submit</div>
</section>

<!-- footer -->
<div class="abs brand" style="top:3420px;left:111px;width:200px;font-size:32px">Marwick<small>JEWELERS</small></div>
<div class="abs fcol" style="left:426px"><h4>Navigation</h4><ul><li>Company</li><li>Custom Jewelery Services</li><li>Jewelery Repair Services</li><li>Resources</li><li>Showcase</li><li>Gallery</li><li>Engraving &amp; Trophies</li><li>Gift Ideas</li></ul></div>
<div class="abs fcol" style="left:678px"><h4>Hours</h4><p><b style="font-weight:500;color:var(--ink)">Monday to Friday</b><br>8:30 a.m - 9:00 p.m.<br><b style="font-weight:500;color:var(--ink)">Saturday &amp; Sunday</b><br>Closed</p></div>
<div class="abs fcol" style="left:900px"><h4>Contact</h4><p>Phone:</p><p style="font-size:13px;margin:6px 0 10px">+1 (555) 010 2244</p><p>Email:</p><p style="font-size:13px;margin:6px 0 10px">info@marwickjewelers.com</p><p>Address:</p><p style="font-size:13px;margin-top:6px">48 Linden Ave, Harrowgate, MN</p></div>
<div class="abs copy">© 2022 <b>Marwickjewelers</b> . All Rights Reserved.</div>
<div class="abs dot" style="left:1040px;top:3616px"></div>
<div class="abs dot" style="left:1070px;top:3616px"></div>

</body>
</html>
```